Company web site

Looking for a full responsive(mobile friendly) wordpress implementation

Some material is in the website -- brelvanto.wordpress.com

But looking for a template more consistent with the logo design, and more future looking.

Target Market(s)

Enterprise Clients

Industry/Entity Type

It Company

Font styles to use
Sans Serif

Colors
33a6d7
0255a3
0455a3
cfdeed
85abd2
3176b5

Requirements
Must have
• about, contact information, partner page, success stories, customer testimonials. links to social presence.
• pricing information

```html
<!DOCTYPE html>
<html lang="en">
<head>
<meta charset="utf-8">
<title>Brelvanto — IoT Enterprise Solutions</title>
<link href="https://fonts.googleapis.com/css2?family=Lato:wght@400;700;900&family=Michroma&family=Play:wght@700&display=swap" rel="stylesheet">
<style>
:root{
  --sky:#33a6d7;
  --navy:#0255a3;
  --navy-2:#0455a3;
  --mist:#cfdeed;
  --steel:#85abd2;
  --band:#3176b5;
  --ink:#1d1d1d;
  --text:#555;
  --soft:#f1f1f1;
  --line:#d6d6d6;
  --icon:#555a60;
}
*{box-sizing:border-box;margin:0;padding:0}
html,body{width:1200px;height:3488px;overflow:hidden}
body{position:relative;background:#fff;font-family:'Lato',sans-serif;color:var(--text)}
.abs{position:absolute}
section,header,footer{position:absolute;left:0;width:1200px}

/* header */
.site-header{top:0;height:121px;background:#fff}
.brand{left:98px;top:80px;font:900 30px 'Lato',sans-serif;color:var(--navy);display:flex;align-items:center;gap:10px}
.brand .dot{width:24px;height:24px;border-radius:50%;background:var(--sky)}
.contact-chip{top:24px;display:flex;gap:12px;align-items:flex-start}
.contact-chip .lbl{font:700 15px 'Lato',sans-serif;color:#444;letter-spacing:.5px}
.contact-chip .val{font:700 16px 'Lato',sans-serif;color:var(--sky)}
.main-nav{position:absolute;top:91px;left:435px;display:flex;align-items:center;font:700 16px 'Lato',sans-serif;color:#333}
.main-nav a{color:#333;text-decoration:none}

/* hero */
.hero{top:121px;height:500px}
.hero-visual{position:absolute;inset:0;background:radial-gradient(ellipse at 78% 60%,#5f7891 0%,#2a3d52 35%,#0e1826 70%,#070c14 100%)}
.hero-title{left:0;width:1200px;top:506px;text-align:center;font:700 34px 'Play',sans-serif;color:#fff;letter-spacing:1px;text-shadow:0 2px 4px rgba(0,0,0,.5)}
.hero-dots{top:580px;left:578px;display:flex;gap:8px}
.hero-dots span{width:12px;height:12px;border-radius:50%;background:#fff}
.hero-dots span:first-child{background:var(--sky)}

/* welcome */
.welcome{top:621px;height:384px;background:#f3f3f3}
.welcome h1{position:absolute;top:45px;width:1200px;text-align:center;font:400 38px 'Michroma',sans-serif;color:#111}
.welcome h1 .hl{color:var(--sky)}
.welcome .lead{position:absolute;top:132px;width:1200px;text-align:center;font:700 16px 'Lato',sans-serif;color:#222}
.welcome .body{position:absolute;top:172px;left:98px;width:1005px;font:400 14.5px/26px 'Lato',sans-serif;color:#555;text-align:center}
.btn{position:absolute;display:flex;align-items:center;justify-content:center;gap:12px;border-radius:22px;font:700 15px 'Lato',sans-serif;color:#fff}
.btn .arrow{width:26px;height:26px;border-radius:50%;background:#fff;display:flex;align-items:center;justify-content:center}
.welcome .btn{top:292px;left:540px;width:124px;height:40px;background:var(--navy)}

/* lifecycle */
.lifecycle{top:1005px;height:716px;background:#fff}
.lifecycle h2{position:absolute;top:50px;width:1200px;text-align:center;font:700 31px 'Lato',sans-serif;color:#111}
.lifecycle h2 .hl{color:var(--sky);font-weight:400}
.lifecycle .sub{position:absolute;top:105px;width:1200px;text-align:center;font:700 16px 'Lato',sans-serif;color:#222}
.stage{position:absolute;background:linear-gradient(#fff,#eceff2);border:1px solid #d5d8dc;box-shadow:0 2px 4px rgba(0,0,0,.12);padding:8px 12px;font:400 13px/18px 'Lato',sans-serif;color:#333}
.stage .num{position:absolute;font:400 54px 'Lato',sans-serif;color:var(--mist);top:8px}
.stage ul{list-style:none;position:relative}
.stage li::before{content:"•";color:#333;margin-right:5px}
.stage-label{position:absolute;font:700 15px 'Lato',sans-serif;color:var(--sky)}
.stage-icon{position:absolute;width:46px;height:46px;border-radius:50%;background:var(--icon);border:3px solid #fff;box-shadow:0 0 0 1px #bbb}
.hub-name{position:absolute;left:450px;top:428px;width:340px;text-align:center;font:900 40px 'Lato',sans-serif;color:var(--sky)}

/* band */
.promo{top:1721px;height:251px;background:linear-gradient(90deg,var(--band),var(--navy))}
.promo h2{position:absolute;top:40px;width:1200px;text-align:center;font:400 33px/46px 'Michroma',sans-serif;color:#fff;letter-spacing:1px}
.promo .btn{top:159px;left:530px;width:158px;height:40px;background:var(--sky)}

/* how it works */
.how{top:1972px;height:568px;background:#fff}
.sec-title{position:absolute;width:1200px;text-align:center;font:700 34px 'Lato',sans-serif;color:#555}
.sec-title .hl{color:var(--sky);font-weight:400}
.sec-rule{position:absolute;left:385px;width:430px;height:1px;background:#ccc}
.step-label{position:absolute;font:700 18px 'Lato',sans-serif;color:#333}
.step-list{position:absolute;list-style:none;font:400 14px/22px 'Lato',sans-serif;color:#333}
.step-list li::before{content:"• "}

/* testimonials */
.testimonials{top:2540px;height:326px;background:#f1f1f1}
.quote{position:absolute;font:700 14.5px/22px 'Lato',sans-serif;color:#555;width:356px}
.quote .mark{color:var(--sky);font:900 34px/10px 'Lato',sans-serif;vertical-align:-12px;margin-right:4px}
.author{position:absolute;font:400 14px 'Lato',sans-serif;color:#777}
.portrait{position:absolute;width:124px;height:124px;border-radius:50%;border:5px solid var(--sky);background:radial-gradient(circle at 50% 40%,#e8d2bf,#a9876d 70%,#6d5746)}
.chev{position:absolute;font:300 60px 'Lato',sans-serif;color:#ccc}

/* partners */
.partners{top:2866px;height:274px;background:#fff}
.partner{position:absolute;top:135px;height:86px;border:1px solid #ddd;display:flex;align-items:center;justify-content:center;font:700 22px 'Lato',sans-serif;color:#222;gap:8px}
.partner .sq{width:14px;height:14px;background:#222}

/* footer */
.site-footer{top:3140px;height:307px;background:var(--navy-2);color:#fff}
.f-head{position:absolute;top:44px;font:700 18px 'Lato',sans-serif;color:#fff}
.f-head .hl{color:var(--sky);font-weight:400}
.f-links{position:absolute;top:94px;left:98px;list-style:none;font:400 13px/31.7px 'Lato',sans-serif}
.f-links li::before{content:"• "}
.f-contact{position:absolute;top:90px;left:326px;font:400 14px/20px 'Lato',sans-serif}
.f-row{display:flex;align-items:center;gap:10px;margin-top:18px}
.map{position:absolute;left:568px;top:88px;width:297px;height:184px;background:linear-gradient(135deg,#eef0ea,#dfe3dc 50%,#f4f2ec);border:4px solid #fff}
.f-brand{position:absolute;left:945px;top:140px;width:180px;text-align:center;font:900 26px 'Lato',sans-serif;color:#fff}
.social{position:absolute;top:188px;left:955px;display:flex;gap:8px}
.social span{width:30px;height:30px;border-radius:50%;background:var(--steel);border:2px solid #fff}
.copyright{position:absolute;top:3447px;left:0;width:1200px;height:41px;background:var(--sky);color:#fff;text-align:center;font:400 13px/41px 'Lato',sans-serif}
</style>
</head>
<body>

<header class="site-header">
  <div class="abs brand"><span class="dot"></span>Brelvanto</div>
  <div class="abs contact-chip" style="left:633px">
    <svg width="32" height="32" viewBox="0 0 24 24"><path d="M6.6 10.8a15 15 0 0 0 6.6 6.6l2.2-2.2c.3-.3.7-.4 1-.2 1.1.4 2.3.6 3.6.6.6 0 1 .4 1 1V20c0 .6-.4 1-1 1A17 17 0 0 1 3 4c0-.6.4-1 1-1h3.5c.6 0 1 .4 1 1 0 1.3.2 2.5.6 3.6.1.3 0 .7-.2 1z" fill="none" stroke="#33a6d7" stroke-width="1.6"/></svg>
    <div><div class="lbl">CALL US</div><div class="val">+1-(555) 014-3920</div></div>
  </div>
  <div class="abs contact-chip" style="left:891px">
    <svg width="36" height="32" viewBox="0 0 26 22"><path d="M1 3h24v16H1z M1 3l12 9 12-9" fill="none" stroke="#33a6d7" stroke-width="1.6"/></svg>
    <div><div class="lbl">MAIL US</div><div class="val">info@brelvanto.com</div></div>
  </div>
  <nav class="main-nav">
    <svg width="22" height="20" viewBox="0 0 22 20" style="margin-right:26px"><path d="M11 1 1 10h3v9h5v-6h4v6h5v-9h3z" fill="#33a6d7"/></svg>
    <a style="margin-right:34px">About</a>
    <a style="margin-right:34px">Partner</a>
    <a style="margin-right:34px">Success Stories</a>
    <a style="margin-right:34px">Customer Testimonials</a>
    <a>Contact</a>
  </nav>
</header>

<section class="hero">
  <div class="hero-visual" role="img" aria-label="Night view of the globe from space wrapped in a glowing network of connection lines"></div>
</section>
<div class="abs hero-title">Bridging Connected Devices With Enterprise Solutions</div>
<div class="abs hero-dots"><span></span><span></span><span></span></div>

<section class="welcome">
  <h1>WelcomeTo <span class="hl">Brelvanto</span></h1>
  <p class="lead">Founded in 2016 by industry veterans, Brelvanto is geared to provide integrated solutions for the IoT industry</p>
  <p class="body">Lorem ipsum dolor sit amet, consectetuer adipiscing elit, sed diam nonummy nibh euismod tincidunt ut laoreet dolore magna aliquam erat volutpat. Ut wisi enim ad minim veniam, quis nostrud exerci tation ullamcorper suscipit lobortis nisl ut aliquip ex ea commodo consequat. Duis autem vel eum iriure dolor in hendrerit in vulputate velit esse molestie consequat, vel illum dolore eu feugiat nulla facilisis at vero</p>
  <div class="btn">Read More <span class="arrow"><svg width="10" height="12" viewBox="0 0 10 12"><path d="M2 1l6 5-6 5" fill="none" stroke="#0255a3" stroke-width="2.4"/></svg></span></div>
</section>

<section class="lifecycle">
  <h2>Brelvanto Ensures End-to-end Product <span class="hl">Lifecycle Management</span></h2>
  <p class="sub">Closely engage with users throughout the entire process and increase customer lifetime value.</p>

  <svg class="abs" style="left:0;top:0" width="1200" height="716" viewBox="0 1005 1200 716">
    <g fill="none" stroke="#9a9a9a" stroke-width="1.5" stroke-dasharray="5 4">
      <polyline points="620,1265 620,1272"/>
      <polyline points="354,1305 440,1305 484,1336"/>
      <polyline points="849,1290 800,1290 756,1336"/>
      <polyline points="372,1448 410,1448 445,1419"/>
      <polyline points="833,1450 810,1450 795,1419"/>
      <polyline points="400,1605 430,1605 466,1539"/>
      <polyline points="802,1605 780,1605 774,1539"/>
    </g>
    <circle cx="620" cy="1450" r="176" fill="#e6e6e6"/>
    <g fill="#33a6d7" stroke="#fff" stroke-width="3">
      <circle cx="620" cy="1272" r="10"/>
      <circle cx="484" cy="1336" r="10"/>
      <circle cx="756" cy="1336" r="10"/>
      <circle cx="445" cy="1419" r="10"/>
      <circle cx="795" cy="1419" r="10"/>
      <circle cx="466" cy="1539" r="10"/>
      <circle cx="774" cy="1539" r="10"/>
    </g>
  </svg>
  <div class="hub-name">Brelvanto</div>

  <div class="stage-label" style="left:642px;top:200px">Use</div>
  <div class="stage" style="left:481px;top:222px;width:240px;height:62px;text-align:right">
    <span class="num" style="left:6px;top:0">4</span>
    <ul><li>Customer web portal &amp; mobile apps</li><li>Notifications, social identity and advanced IoT services</li></ul>
  </div>
  <div class="stage-icon" style="left:690px;top:186px"></div>

  <div class="stage-icon" style="left:98px;top:247px"></div>
  <div class="stage-label" style="left:158px;top:278px">Provision</div>
  <div class="stage" style="left:112px;top:298px;width:242px;height:62px">
    <span class="num" style="right:10px">3</span>
    <ul><li>Simplify consumer experience during device activation</li><li>P2P communication via Linkwell</li></ul>
  </div>

  <div class="stage-icon" style="left:1050px;top:243px"></div>
  <div class="stage-label" style="left:985px;top:274px">Support</div>
  <div class="stage" style="left:849px;top:296px;width:240px;height:58px;text-align:right">
    <span class="num" style="left:8px">5</span>
    <ul><li>In app chat, ticketing system and call center integration</li></ul>
  </div>

  <div class="stage-icon" style="left:112px;top:395px"></div>
  <div class="stage-label" style="left:172px;top:420px">Sell</div>
  <div class="stage" style="left:112px;top:438px;width:260px;height:66px">
    <span class="num" style="right:10px">2</span>
    <ul><li>End user tracking in CRM</li><li>Social identity for proactive marketing</li></ul>
  </div>

  <div class="stage-icon" style="left:1046px;top:398px"></div>
  <div class="stage-label" style="left:960px;top:424px">Monetize</div>
  <div class="stage" style="left:833px;top:442px;width:237px;height:70px;text-align:right">
    <span class="num" style="left:8px">6</span>
    <ul><li>Recurrent user billing</li><li>Additional services &amp; payment options.</li></ul>
  </div>

  <div class="stage-icon" style="left:150px;top:542px"></div>
  <div class="stage-label" style="left:210px;top:570px">Manufacture</div>
  <div class="stage" style="left:144px;top:590px;width:256px;height:66px">
    <span class="num" style="right:10px">1</span>
    <ul><li>Secure manufacturing process</li><li>Device traceability in ERP</li></ul>
  </div>

  <div class="stage-icon" style="left:1006px;top:544px"></div>
  <div class="stage-label" style="left:920px;top:570px">Maintain</div>
  <div class="stage" style="left:802px;top:590px;width:256px;height:66px;text-align:right">
    <span class="num" style="left:8px">7</span>
    <ul><li>Device health check</li><li>Software and security updates</li></ul>
  </div>
</section>

<section class="promo">
  <h2>A complete package that links IoT clouds<br>with enterprise software solutions</h2>
  <div class="btn">Get Started <span class="arrow"><svg width="10" height="12" viewBox="0 0 10 12"><path d="M2 1l6 5-6 5" fill="none" stroke="#33a6d7" stroke-width="2.4"/></svg></span></div>
</section>

<section class="how">
  <h2 class="sec-title" style="top:42px">How It <span class="hl">Works</span></h2>
  <div class="sec-rule" style="top:98px"></div>

  <svg class="abs" style="left:0;top:0" width="1200" height="568" viewBox="0 1972 1200 568">
    <g fill="none" stroke="#33a6d7" stroke-width="4">
      <polyline points="163,2365 470,2228 735,2365 1040,2228"/>
    </g>
    <g fill="#fff" stroke="#33a6d7" stroke-width="5">
      <circle cx="163" cy="2365" r="56"/>
      <circle cx="470" cy="2228" r="56"/>
      <circle cx="735" cy="2365" r="56"/>
      <circle cx="1040" cy="2228" r="56"/>
    </g>
    <g fill="#33a6d7" stroke="#fff" stroke-width="3">
      <circle cx="201" cy="2324" r="9"/>
      <circle cx="510" cy="2267" r="9"/>
      <circle cx="775" cy="2326" r="9"/>
      <circle cx="990" cy="2252" r="9"/>
    </g>
    <path d="M138 2376 l25 8 25-8 v-30 l-25 8 -25-8z M163 2354 v30" fill="none" stroke="#333" stroke-width="4"/>
    <circle cx="163" cy="2336" r="9" fill="#333"/>
    <g fill="none" stroke="#333" stroke-width="6" stroke-linecap="round">
      <rect x="443" y="2218" width="34" height="18" rx="9" transform="rotate(-45 460 2227)"/>
      <rect x="463" y="2220" width="34" height="18" rx="9" transform="rotate(-45 480 2229)"/>
    </g>
    <g fill="none" stroke="#333" stroke-width="6">
      <circle cx="728" cy="2370" r="14"/>
      <circle cx="752" cy="2348" r="8"/>
    </g>
    <g stroke="#333" stroke-width="5" stroke-linecap="round">
      <line x1="728" y1="2346" x2="728" y2="2352"/><line x1="728" y1="2388" x2="728" y2="2394"/>
      <line x1="704" y1="2370" x2="710" y2="2370"/><line x1="746" y1="2370" x2="752" y2="2370"/>
    </g>
    <g stroke="#333" stroke-width="4">
      <line x1="1040" y1="2228" x2="1019" y2="2206"/><line x1="1040" y1="2228" x2="1063" y2="2208"/>
      <line x1="1040" y1="2228" x2="1021" y2="2250"/><line x1="1040" y1="2228" x2="1061" y2="2250"/>
    </g>
    <g fill="#333">
      <circle cx="1040" cy="2228" r="9"/><circle cx="1019" cy="2206" r="6"/><circle cx="1063" cy="2208" r="6"/>
      <circle cx="1021" cy="2250" r="6"/><circle cx="1061" cy="2250" r="6"/>
    </g>
    <g font-family="Lato, sans-serif" font-weight="700" fill="#333">
      <text x="303" y="2320" font-size="30" transform="rotate(-30 312 2310)">×</text>
      <text x="579" y="2297" font-size="30" transform="rotate(30 588 2287)">×</text>
      <text x="862" y="2283" font-size="32" transform="rotate(-30 872 2273)">=</text>
    </g>
  </svg>

  <div class="step-label" style="left:420px;top:164px">Connect</div>
  <div class="step-label" style="left:135px;top:274px">Learn</div>
  <div class="step-label" style="left:693px;top:274px">Integrate</div>
  <div class="step-label" style="left:937px;top:164px">Connected Product</div>

  <ul class="step-list" style="left:123px;top:460px"><li>Properties</li><li>Actions</li><li>Events</li></ul>
  <ul class="step-list" style="left:424px;top:334px"><li>Skyframe IoT</li><li>Cobalt IoT</li><li>Linkwell</li><li>Gridnet</li><li>Thingset</li><li style="list-style:none">... and others</li></ul>
  <ul class="step-list" style="left:628px;top:458px"><li>CRM systems</li><li>Social login</li><li>Billing</li></ul>
  <ul class="step-list" style="left:772px;top:458px"><li>HelpDeskly</li><li>Flowrule</li><li style="list-style:none">... and many others</li></ul>
</section>

<section class="testimonials">
  <h2 class="sec-title" style="top:46px">Client <span class="hl">Testimonials</span></h2>
  <div class="sec-rule" style="top:102px"></div>
  <div class="chev" style="left:56px;top:158px">‹</div>
  <div class="chev" style="left:1110px;top:158px">›</div>

  <div class="portrait" style="left:105px;top:136px" role="img" aria-label="Portrait photo of a smiling male client"></div>
  <p class="quote" style="left:226px;top:148px"><span class="mark">“</span>Duis autem vel eumk iriure dolor at veromoli eros dignissim qui blandit praesent luptatum hok quis nostrud exercitation ullamcorper susc zzrilm deleni augue duis facilisis.</p>
  <div class="author" style="left:236px;top:256px">- Mr. Arlen Voss</div>

  <div style="position:absolute;left:623px;top:140px;width:1px;height:140px;background:#ddd"></div>

  <div class="portrait" style="left:652px;top:136px" role="img" aria-label="Portrait photo of a smiling female client"></div>
  <p class="quote" style="left:774px;top:148px"><span class="mark">“</span>Duis autem vel eumk iriure dolor at veromoli eros dignissim qui blandit praesent luptatum hok quis nostrud exercitation ullamcorper susc zzrilm deleni augue duis facilisis.</p>
  <div class="author" style="left:784px;top:256px">- Mrs. Petra Lind</div>
</section>

<section class="partners">
  <h2 class="sec-title" style="top:46px">Our <span class="hl">Partners</span></h2>
  <div class="sec-rule" style="top:102px"></div>
  <div class="chev" style="left:44px;top:128px">‹</div>
  <div class="chev" style="left:1124px;top:128px">›</div>
  <div class="partner" style="left:98px;width:188px">Ledgerly</div>
  <div class="partner" style="left:302px;width:189px">Nimbrel</div>
  <div class="partner" style="left:507px;width:186px">Arcona</div>
  <div class="partner" style="left:709px;width:187px"><span class="sq"></span>Vestholm</div>
  <div class="partner" style="left:912px;width:188px">Quorix</div>
</section>

<footer class="site-footer">
  <div class="f-head" style="left:98px">Quick <span class="hl">Links</span></div>
  <ul class="f-links"><li>Home</li><li>About</li><li>Partner</li><li>Success Stories</li><li>Customer Testimonials</li><li>Contact</li></ul>

  <div class="f-head" style="left:326px">Contact <span class="hl">Details</span></div>
  <div class="f-contact">
    <div>Brelvanto<br>418 Harlow Ave<br>Fernbrook, CA 90210</div>
    <div class="f-row"><svg width="16" height="16" viewBox="0 0 24 24"><path d="M6.6 10.8a15 15 0 0 0 6.6 6.6l2.2-2.2c.3-.3.7-.4 1-.2 1.1.4 2.3.6 3.6.6.6 0 1 .4 1 1V20c0 .6-.4 1-1 1A17 17 0 0 1 3 4c0-.6.4-1 1-1h3.5c.6 0 1 .4 1 1 0 1.3.2 2.5.6 3.6.1.3 0 .7-.2 1z" fill="#33a6d7"/></svg>+1-(555) 014-3920</div>
    <div class="f-row"><svg width="16" height="16" viewBox="0 0 24 24"><rect x="3" y="6" width="18" height="14" rx="2" fill="#33a6d7"/><rect x="7" y="2" width="10" height="6" fill="#33a6d7"/></svg>+1-(555) 014-3920</div>
    <div class="f-row"><svg width="16" height="14" viewBox="0 0 26 22"><path d="M1 3h24v16H1z M1 3l12 9 12-9" fill="none" stroke="#33a6d7" stroke-width="2.4"/></svg>info@brelvanto.com</div>
  </div>

  <div class="f-head" style="left:568px">Location <span class="hl">Map</span></div>
  <div class="map" role="img" aria-label="Street map showing the office location with a red pin"></div>

  <div class="f-brand">Brelvanto</div>
  <div class="social" role="img" aria-label="Social media links">
    <span></span><span></span><span></span><span></span>
  </div>
</footer>
<div class="copyright">Copyright © 2017 Brelvanto. All Rights Reserved.</div>

</body>
</html>
```